Web Developer Needs a Business Card Design

I need a personal business card design that represents me as a web developer for potential employers. I would like the background to be a dark color on the front for contrast with my logo and name. The back will have all my information along with a smaller version of the logo. I want something with a modern look and feel, not too conservative. This will be used for potential employers and freelance work.

Industry/Entity Type

Business

Contact Information for Business Card

Front should have my logo and name. The back should have all my personal information which would include: name: Tom Varulek, phone: 570-614-3098, email: tomvarulek@quillbox.net, website url: www.tomvarulek.net, logo, web developer.

Font styles to use
Sans Serif

Requirements
Must have
• Must include my logo. The color palette base color will be the logo color.

```html
<!DOCTYPE html>
<html lang="en">
<head>
<meta charset="utf-8">
<title>Tom Varulek — Business Card</title>
<link rel="stylesheet" href="https://fonts.googleapis.com/css2?family=Oxygen:wght@400;700&display=swap">
<style>
  :root {
    --canvas: #6b5a48;
    --card: #060606;
    --card-sheen: #1c1c1c;
    --mint: #74e0cb;
    --mint-soft: #8fd6c6;
    --white: #ffffff;
  }
  * { margin: 0; padding: 0; box-sizing: border-box; }
  html, body {
    width: 1200px; height: 902px; overflow: hidden;
    background: var(--canvas);
    font-family: "Oxygen", sans-serif;
  }
  .stage { position: relative; width: 1200px; height: 902px; }
  .card {
    position: absolute; width: 560px; height: 320px;
    background: linear-gradient(135deg, var(--card-sheen) 0%, var(--card) 45%);
    border-radius: 4px; overflow: hidden;
    box-shadow: 0 10px 30px rgba(0,0,0,.45);
  }
  .card--front { left: 70px; top: 70px; }
  .card--back { left: 570px; top: 510px; }

  .logo-mark {
    display: flex; align-items: center; justify-content: center; gap: 10px;
    color: var(--mint); font-weight: 700;
  }
  .logo-mark__circle {
    border: 5px solid var(--mint); border-radius: 50%;
  }
  .card--front .logo-mark {
    position: absolute; left: 0; right: 0; top: 70px;
  }
  .card--front .logo-mark__circle { width: 70px; height: 70px; }
  .card--front .logo-mark__name { font-size: 30px; }
  .card--front .card__name {
    position: absolute; left: 0; right: 0; top: 200px;
    text-align: center; color: var(--mint); font-size: 34px; font-weight: 400;
  }

  .card--back .logo-mark {
    position: absolute; left: 40px; top: 120px;
  }
  .card--back .logo-mark__circle { width: 50px; height: 50px; border-width: 4px; }
  .card--back .logo-mark__name { font-size: 22px; }
  .identity { position: absolute; left: 250px; top: 34px; }
  .identity__name { color: var(--mint); font-size: 32px; }
  .identity__role { color: var(--white); font-size: 17px; margin: 2px 0 0 30px; }
  .contact-list { list-style: none; position: absolute; left: 280px; top: 112px; }
  .contact-list li {
    display: flex; align-items: center; gap: 10px;
    color: var(--white); font-size: 16px; margin-bottom: 8px;
  }
  .contact-list svg { width: 16px; height: 16px; flex: none; }
  .band { position: absolute; left: 0; bottom: 0; width: 560px; height: 130px; }
</style>
</head>
<body>
<main class="stage">
  <section class="card card--front" aria-label="Card front">
    <div class="logo-mark">
      <span class="logo-mark__circle"></span>
      <span class="logo-mark__name">Varulek</span>
    </div>
    <p class="card__name">Tom Varulek</p>
  </section>

  <section class="card card--back" aria-label="Card back">
    <div class="identity">
      <h1 class="identity__name">Tom Varulek</h1>
      <p class="identity__role">web developer</p>
    </div>
    <ul class="contact-list">
      <li>
        <svg viewBox="0 0 16 16"><rect width="16" height="16" rx="2" fill="#fff"/><path d="M4 3l2.5 0 1 3-1.5 1c.7 1.4 1.6 2.3 3 3l1-1.5 3 1V12c0 .6-.5 1-1 1C7.5 13 3 8.5 3 4c0-.5.4-1 1-1z" fill="#060606"/></svg>
        570-614-3098
      </li>
      <li>
        <svg viewBox="0 0 16 16"><rect width="16" height="16" rx="2" fill="#fff"/><circle cx="8" cy="8" r="4.5" fill="none" stroke="#060606" stroke-width="1.4"/><path d="M3.5 8h9M8 3.5c-2 2.5-2 6.5 0 9M8 3.5c2 2.5 2 6.5 0 9" fill="none" stroke="#060606" stroke-width="1"/></svg>
        www.tomvarulek.net
      </li>
      <li>
        <svg viewBox="0 0 16 16"><rect width="16" height="16" rx="2" fill="#fff"/><rect x="3" y="5" width="10" height="7" fill="none" stroke="#060606" stroke-width="1.3"/><path d="M3 5l5 4 5-4" fill="none" stroke="#060606" stroke-width="1.3"/></svg>
        tomvarulek@quillbox.net
      </li>
    </ul>
    <div class="logo-mark">
      <span class="logo-mark__circle"></span>
      <span class="logo-mark__name">Varulek</span>
    </div>
    <svg class="band" viewBox="0 0 560 130" preserveAspectRatio="none" aria-hidden="true">
      <path d="M0 130 L0 120 Q300 40 560 10 L560 130 Z" fill="var(--mint-soft)"/>
      <path d="M0 112 Q300 34 560 4" fill="none" stroke="var(--white)" stroke-width="4"/>
    </svg>
  </section>
</main>
</body>
</html>
```